business card for horse saddlery

after a new business card for our saddlery, i will add 2 logos we have previously used and they can be used (or not) . Any images can be used from our website also at www.harrowfields.net.au, I have also added our brand logo, which may be good to incorporate on back ? we have over 15, 000 items online, ship Australia Wide.

Target Market(s)

horse owners

Industry/Entity Type

Retail - Equestrian

Contact Information for Business Card

Harrowfield Horse Supplies, 1300 48 62 90, www.harrowfields.net.au, 27 Lindqvist Rd Marrowbank Q 4587

Requirements
Must have
• trailgem is our brand so trailgem logo on back as 'distributers of', easy to read
Nice to have
• professional but fun
Should not have
• double sided (description wont save double sided)

```html
<!DOCTYPE html>
<html lang="en">
<head>
<meta charset="utf-8">
<title>Harrowfield Horse Supplies – Business Card</title>
<link rel="stylesheet" href="https://fonts.googleapis.com/css2?family=Montserrat:wght@700&family=Open+Sans:wght@400;600&display=swap">
<style>
  :root {
    --backdrop: #232323;
    --card: #ffffff;
    --amber: #fbb21c;
    --navy: #2b3f86;
    --ink: #1b1b1b;
    --icon: #3d7fd0;
    --photo-dark: #0d0d0d;
    --photo-light: #8d9096;
  }
  * { box-sizing: border-box; margin: 0; padding: 0; }
  html, body {
    width: 1200px; height: 780px; overflow: hidden;
    background: var(--backdrop);
  }
  .canvas {
    width: 1200px; height: 780px;
    display: flex; justify-content: center; align-items: center; gap: 70px;
  }
  .card {
    width: 390px; height: 680px;
    background: var(--card);
    border: 3px solid var(--amber);
    position: relative;
    display: flex; flex-direction: column; align-items: center;
    font-family: "Open Sans", Arial, sans-serif;
    color: var(--ink);
  }
  .card--back { border-radius: 195px 195px 0 0; justify-content: center; }
  .card--front { border-radius: 0 0 195px 195px; padding-top: 60px; }

  /* brand lockup: plain circle + name */
  .brand { display: flex; align-items: center; gap: 14px; }
  .brand__disc { border-radius: 50%; background: var(--amber); flex: none; }
  .brand__name {
    font-family: "Open Sans", Arial, sans-serif;
    font-weight: 600; color: var(--navy); line-height: 1.1;
  }
  .card--back .brand { flex-direction: column; gap: 22px; }
  .card--back .brand__disc { width: 150px; height: 150px; }
  .card--back .brand__name { font-size: 34px; text-align: center; }
  .card--front .brand__disc { width: 64px; height: 64px; }
  .card--front .brand__name { font-size: 24px; }

  .portrait {
    margin-top: 44px;
    width: 170px; height: 170px; border-radius: 50%;
    border: 3px solid var(--amber);
    background: radial-gradient(circle at 40% 50%, var(--photo-light) 0%, #4a4c50 38%, var(--photo-dark) 72%);
  }
  .person__name {
    margin-top: 18px;
    font-family: "Montserrat", Arial, sans-serif; font-weight: 700;
    font-size: 30px; color: var(--amber);
  }
  .person__role { font-size: 17px; font-weight: 600; margin-top: 2px; }

  .contact-icons { display: flex; gap: 14px; margin-top: 12px; }
  .icon { width: 24px; height: 24px; display: block; }
  .contact__phone { font-size: 26px; font-weight: 600; margin-top: 6px; letter-spacing: .5px; }
  .contact__web { font-size: 17px; font-weight: 600; }
  .contact__pin { margin-top: 16px; }
  .contact__address { font-size: 17px; font-weight: 600; text-align: center; line-height: 1.35; margin-top: 6px; }

  .partners { display: flex; align-items: center; gap: 28px; margin-top: 22px; }
  .partner-badge { width: 46px; height: 30px; border-radius: 6px; background: var(--icon); opacity: .75; }
  .partner-name {
    font-family: "Open Sans", Arial, sans-serif; font-weight: 400;
    font-size: 15px; color: var(--navy); letter-spacing: 1px; text-transform: uppercase;
  }
</style>
</head>
<body>
<main class="canvas">

  <section class="card card--back">
    <div class="brand">
      <span class="brand__disc"></span>
      <span class="brand__name">Harrowfield<br>Horse Supplies</span>
    </div>
  </section>

  <section class="card card--front">
    <div class="brand">
      <span class="brand__disc"></span>
      <span class="brand__name">Harrowfield<br>Horse Supplies</span>
    </div>

    <div class="portrait" role="img" aria-label="Photo of a grey horse wearing a bridle against a black background"></div>

    <h1 class="person__name">Mirela Hanakova</h1>
    <p class="person__role">Horse owners</p>

    <div class="contact-icons">
      <svg class="icon" viewBox="0 0 24 24" aria-hidden="true">
        <circle cx="12" cy="12" r="12" fill="var(--icon)"/>
        <path d="M8.5 6.5l2 2-1.2 1.5a7 7 0 0 0 4.7 4.7l1.5-1.2 2 2-1.3 1.8c-4.5-.3-9.2-5-9.5-9.5z" fill="#fff"/>
      </svg>
      <svg class="icon" viewBox="0 0 24 24" aria-hidden="true">
        <circle cx="12" cy="12" r="12" fill="var(--icon)"/>
        <circle cx="12" cy="12" r="6" fill="none" stroke="#fff" stroke-width="1.5"/>
        <path d="M6 12h12M12 6c-2.5 3-2.5 9 0 12M12 6c2.5 3 2.5 9 0 12" fill="none" stroke="#fff" stroke-width="1.2"/>
      </svg>
    </div>
    <p class="contact__phone">1300 48 62 90</p>
    <p class="contact__web">www.harrowfields.net.au</p>

    <svg class="icon contact__pin" viewBox="0 0 24 24" aria-hidden="true">
      <circle cx="12" cy="12" r="12" fill="var(--icon)"/>
      <path d="M12 5a4.5 4.5 0 0 0-4.5 4.5C7.5 13 12 18.5 12 18.5s4.5-5.5 4.5-9A4.5 4.5 0 0 0 12 5z" fill="#fff"/>
      <circle cx="12" cy="9.5" r="1.7" fill="var(--icon)"/>
    </svg>
    <p class="contact__address">27 Lindqvist Rd<br>Marrowbank Q 4587</p>

    <div class="partners">
      <span class="partner-badge" aria-hidden="true"></span>
      <span class="partner-name">Trailgem</span>
    </div>
  </section>

</main>
</body>
</html>
```